Need Business Card for our Real Estate Business with Sales Executive's Picture

PANTONE 484 C ( RED)

PANTONE 2766 C ( BLUE

Industry/Entity Type

Real Estate

Contact Information for Business Card

Name, Mobile, email, & picture of Person
Agency Phone, address, Web address

Requirements
Must have
• Our Logo Colours, Agent Picture,

```html
<!DOCTYPE html>
<html lang="en">
<head>
<meta charset="utf-8">
<title>Meridian Real Estate – Business Card</title>
<link href="https://fonts.googleapis.com/css2?family=Cinzel:wght@400;600&family=Crimson+Text:ital,wght@0,400;1,400&display=swap" rel="stylesheet">
<style>
  :root {
    --navy: #141b4d;
    --red: #9a2a2f;
    --paper: #f4f4f5;
    --paper-edge: #dcdde0;
    --backdrop: #e7e4df;
    --ink: #1a2150;
  }
  * { margin: 0; padding: 0; box-sizing: border-box; }
  html, body { width: 1200px; height: 780px; overflow: hidden; }
  body { background: var(--backdrop); position: relative; font-family: "Crimson Text", serif; }

  .card {
    position: absolute;
    border-radius: 16px;
    overflow: hidden;
    box-shadow: 0 10px 28px rgba(0,0,0,.18);
  }

  /* Front: portrait with agent photo */
  .card-front {
    left: 110px; top: 100px; width: 330px; height: 578px;
    background: radial-gradient(ellipse at 55% 35%, #ffffff 0%, #e9e9ea 60%, #d6d7d9 100%);
  }
  .agent-photo {
    position: absolute; left: 30px; top: 60px; width: 280px; height: 420px;
    background: linear-gradient(170deg, #c9cdd6 0%, #3e58b8 40%, #2c44a0 100%);
    border-radius: 140px 140px 0 0;
  }
  .name-band {
    position: absolute; left: 0; bottom: 0; width: 100%; height: 98px;
    background: var(--navy);
    border-top: 4px solid var(--red);
    box-shadow: 0 -8px 0 -4px #fff, 0 -10px 0 -4px var(--red);
    display: flex; flex-direction: column; align-items: center; justify-content: center;
    color: #fff;
  }
  .name-band .agent-name { font-family: "Cinzel", serif; font-size: 26px; letter-spacing: 2px; }
  .name-band .agent-title { font-family: "Cinzel", serif; font-size: 14px; letter-spacing: 3px; margin-top: 2px; }

  /* Back: landscape with brand and contacts */
  .card-back {
    left: 510px; top: 225px; width: 578px; height: 330px;
    background: linear-gradient(135deg, #ffffff 0%, var(--paper) 55%, var(--paper-edge) 100%);
  }
  .brand {
    position: absolute; left: 48px; top: 104px;
    display: flex; align-items: center; gap: 12px;
    color: var(--navy);
  }
  .brand-mark { width: 12px; height: 12px; background: var(--navy); }
  .brand-name { font-family: "Cinzel", serif; font-weight: 600; font-size: 34px; letter-spacing: 3px; line-height: 1; }
  .brand-sub { font-family: "Cinzel", serif; font-weight: 600; font-size: 11px; letter-spacing: 4px; margin-top: 6px; }

  .divider {
    position: absolute; left: 318px; top: 62px; width: 1px; height: 150px;
    background: var(--red);
  }

  .contact-block { position: absolute; left: 344px; top: 58px; }
  .person-name { font-family: "Cinzel", serif; font-size: 22px; color: var(--navy); letter-spacing: 1px; line-height: 28px; }
  .person-title { font-style: italic; font-size: 16px; color: var(--red); margin-bottom: 10px; }
  .contact-list { list-style: none; }
  .contact-list li { display: flex; align-items: center; gap: 8px; font-size: 16px; color: var(--ink); line-height: 24px; }
  .contact-list svg { width: 16px; height: 16px; flex: none; }

  .address {
    position: absolute; left: 48px; bottom: 34px;
    font-size: 17px; color: var(--ink);
  }
</style>
</head>
<body>

  <section class="card card-front">
    <div class="agent-photo" role="img" aria-label="Portrait photo of the agent in a blue suit and striped tie"></div>
    <div class="name-band">
      <div class="agent-name">DANIEL HART</div>
      <div class="agent-title">OWNER</div>
    </div>
  </section>

  <section class="card card-back">
    <div class="brand">
      <span class="brand-mark"></span>
      <div>
        <div class="brand-name">MERIDIAN</div>
        <div class="brand-sub">REAL ESTATE</div>
      </div>
    </div>

    <div class="divider"></div>

    <div class="contact-block">
      <div class="person-name">DANIEL HART</div>
      <div class="person-title">Owner</div>
      <ul class="contact-list">
        <li>
          <svg viewBox="0 0 16 16"><circle cx="8" cy="8" r="8" fill="#9a2a2f"/><rect x="5.5" y="3.5" width="5" height="9" rx="1" fill="none" stroke="#fff" stroke-width="1.2"/></svg>
          (555) 318-2740
        </li>
        <li>
          <svg viewBox="0 0 16 16"><circle cx="8" cy="8" r="8" fill="#9a2a2f"/><rect x="4" y="5" width="8" height="6" fill="none" stroke="#fff" stroke-width="1.2"/><path d="M4 5l4 3.5L12 5" fill="none" stroke="#fff" stroke-width="1.2"/></svg>
          hello@meridianhomes.com
        </li>
        <li>
          <svg viewBox="0 0 16 16"><circle cx="8" cy="8" r="8" fill="#9a2a2f"/><circle cx="8" cy="8" r="4.2" fill="none" stroke="#fff" stroke-width="1.1"/><path d="M3.8 8h8.4M8 3.8v8.4" stroke="#fff" stroke-width="1"/></svg>
          www.meridianhomes.com
        </li>
      </ul>
    </div>

    <div class="address">PO BOX 480 Harbour Lane, 4th street Ashford</div>
  </section>

</body>
</html>
```